Events publishing website

Have increased the budget for Coded website design. Thanks
-
We need a wordpress website for events publishing. The website will be using all different kinds of events (social, business, music etc). The website should allow user to submit the new events. the new events will be published after admin reviewed.
Key menu items & requirements
- New Events (1-show picture, short description & start/end date. User can view more details in another page. 2-have categories, such as locations, free/ticked, event type etc. 3 - allow user to share the events in social website)
- Event organizer list (show the full list and most popular event organizers. users can view the list by categories, similar to above)
- events establishments (allow user to publish events related informations such as equipments, venue informations etc)
- discussion forum
Key functions
-registration page (new users should fill name, location, normal users or event organizer, types of event organizer etc)
-allow user to change locations to view different events
-search function
The functions should be similar to the following, the design should not. The website should not look like a proper website.
http://www.plavorgatherings.example
Reason: Hi All, have extended few days to allow some changes to be made for current design. Thanks

```html
<!DOCTYPE html>
<html lang="en">
<head>
<meta charset="utf-8">
<title>Events</title>
<link href="https://fonts.googleapis.com/css2?family=Ubuntu:wght@400;500&family=Open+Sans:wght@400;600&display=swap" rel="stylesheet">
<style>
  :root {
    --page-bg: #eeebe3;
    --page-bg-light: #f8f7f2;
    --topbar: #111111;
    --teal: #4c8479;
    --teal-dark: #3b6d63;
    --teal-light: #5d958a;
    --teal-text: #2e7a6a;
    --orange: #f2a023;
    --ink: #222222;
    --ink-soft: #444444;
    --line: #bdbdbd;
    --white: #ffffff;
  }
  * { box-sizing: border-box; margin: 0; padding: 0; }
  html, body { width: 1200px; height: 2344px; overflow: hidden; }
  body {
    position: relative;
    font-family: "Open Sans", sans-serif;
    color: var(--ink);
    background: radial-gradient(ellipse at 180px 260px, var(--page-bg-light) 0%, var(--page-bg) 55%, #e8e5dc 100%);
  }
  .abs { position: absolute; }

  /* top strip */
  .top-strip { left: 0; top: 0; width: 1200px; height: 34px; background: var(--topbar); display: flex; align-items: center; padding-left: 33px; font: 600 12px "Open Sans", sans-serif; color: var(--white); letter-spacing: .2px; }
  .top-strip span.sep { margin: 0 10px; color: #aaa; }

  /* brand */
  .brand-name { left: 44px; top: 68px; font: 400 42px "Ubuntu", sans-serif; color: var(--teal-dark); letter-spacing: -.5px; }
  .brand-slogan { left: 48px; top: 116px; font: 400 17px "Ubuntu", sans-serif; color: var(--teal-dark); }

  .account-links { left: 850px; top: 58px; display: flex; gap: 22px; font: 400 16px "Ubuntu", sans-serif; color: var(--teal-dark); align-items: flex-end; }
  .account-links a { display: flex; align-items: flex-end; gap: 5px; color: inherit; text-decoration: none; }
  .account-links svg { fill: var(--teal-dark); }

  .search { left: 833px; top: 109px; width: 342px; height: 40px; display: flex; box-shadow: 0 1px 3px rgba(0,0,0,.15); }
  .search-field { flex: 1; background: var(--white); border: 1px solid #d8d8d8; border-right: 0; font: 400 14px "Ubuntu", sans-serif; color: #666; padding: 10px 12px; }
  .search-go { width: 40px; background: var(--orange); color: var(--white); font: 500 16px "Ubuntu", sans-serif; display: flex; align-items: center; justify-content: center; }

  /* nav */
  .main-nav { left: 34px; top: 170px; width: 1146px; height: 66px; background: linear-gradient(var(--teal-light), var(--teal)); display: flex; align-items: center; border-bottom: 2px solid var(--white); }
  .main-nav a { font: 400 19px "Ubuntu", sans-serif; color: var(--white); text-decoration: none; height: 100%; display: flex; align-items: center; border-right: 1px dotted rgba(255,255,255,.35); }
  .main-nav a:last-child { border-right: 0; }

  /* hero */
  .hero { left: 34px; top: 238px; width: 1146px; height: 356px; background: linear-gradient(90deg, #1c2a3a 0%, #4b5a6a 18%, #2a2a2a 40%, #3a1a10 55%, #c2401a 68%, #e88a24 75%, #5a1810 85%, #2a1a10 100%); }
  .hero-shade { left: 34px; top: 470px; width: 1146px; height: 124px; background: linear-gradient(transparent, rgba(40,25,15,.75)); }
  .hero-arrow { top: 377px; width: 34px; height: 50px; background: var(--white); display: flex; align-items: center; justify-content: center; box-shadow: 0 1px 3px rgba(0,0,0,.25); }
  .hero-arrow.prev { left: 34px; border-radius: 0 25px 25px 0; }
  .hero-arrow.next { left: 1146px; border-radius: 25px 0 0 25px; }

  /* content */
  .content-wrap { left: 34px; top: 594px; width: 1146px; height: 1383px; background: #f4f3ef; }
  .content-panel { left: 45px; top: 602px; width: 1122px; height: 1364px; background: var(--white); border: 1px solid #dedede; }
  .section-title { left: 81px; top: 648px; font: 400 18px "Ubuntu", sans-serif; color: var(--ink); }
  .section-rule { left: 81px; top: 688px; width: 208px; border-top: 1px dotted #666; }

  .area-select { left: 808px; top: 622px; width: 258px; height: 36px; border-radius: 18px; border: 3px solid #ececec; background: var(--white); font: 400 14px "Ubuntu", sans-serif; color: #888; padding: 6px 14px; display: flex; justify-content: space-between; align-items: center; }
  .area-go { left: 1073px; top: 617px; width: 46px; height: 46px; border-radius: 50%; background: #1d1d1d; border: 2px solid #cfcfcf; color: var(--white); font: 400 20px "Ubuntu", sans-serif; display: flex; align-items: center; justify-content: center; }

  .event-card { left: 81px; width: 1052px; }
  .event-photo { position: absolute; left: 0; top: 0; width: 374px; height: 226px; border: 4px solid var(--white); box-shadow: 0 0 4px rgba(0,0,0,.35); }
  .event-details { position: absolute; left: 0; top: 0; width: 1052px; }
  .detail-label { position: absolute; right: 492px; font: 400 17px "Ubuntu", sans-serif; color: var(--ink); white-space: nowrap; }
  .detail-value { position: absolute; left: 577px; font: 400 13px "Open Sans", sans-serif; color: var(--ink); line-height: 25px; width: 480px; }
  .detail-value.title { font: 400 17px "Ubuntu", sans-serif; line-height: 22px; }
  .more-link { position: absolute; left: 945px; font: 400 14px "Ubuntu", sans-serif; color: var(--teal-text); text-decoration: none; }
  .more-link small { font-size: 10px; margin-left: 6px; }
  .card-rule { position: absolute; left: 0; width: 1052px; border-top: 1px dotted var(--line); }

  .pagination { left: 908px; top: 1832px; display: flex; align-items: center; gap: 10px; font: 400 15px "Ubuntu", sans-serif; color: var(--ink); }
  .pagination .current { width: 24px; height: 24px; border-radius: 50%; background: var(--teal); color: var(--white); display: flex; align-items: center; justify-content: center; }
  .pagination .next { margin-left: 10px; }

  /* footer */
  .site-footer { left: 34px; top: 1977px; width: 1146px; height: 367px; background: linear-gradient(#5c958a, #4b8076 60%, #457668); }
  .footer-heading { font: 400 21px "Ubuntu", sans-serif; color: var(--white); }
  .quick-links { left: 84px; top: 2046px; width: 647px; }
  .quick-row { display: flex; height: 33px; align-items: center; border-bottom: 1px dashed rgba(255,255,255,.3); font: 400 14px "Open Sans", sans-serif; color: var(--white); }
  .quick-row span { display: block; }
  .quick-row span:nth-child(1) { width: 128px; padding-left: 5px; }
  .quick-row span:nth-child(2) { width: 166px; }
  .quick-row span:nth-child(3) { width: 164px; }
  .social { left: 800px; top: 2039px; display: flex; gap: 6px; }
  .social span { width: 32px; height: 32px; border-radius: 50%; background: var(--white); display: block; }
  .copyright { left: 59px; top: 2224px; width: 1097px; height: 52px; background: rgba(40,80,72,.45); font: 400 12px "Open Sans", sans-serif; color: var(--white); display: flex; align-items: center; padding-left: 22px; }
</style>
</head>
<body>

<nav class="abs top-strip">
  <span>EVENTS</span><span class="sep">|</span><span>NEWS EVENTS</span><span class="sep">|</span><span>SAVOUR</span><span class="sep">|</span><span>EVENT INTERNATIONAL ART SERIES</span><span class="sep">|</span><span>PLAVOR EVENTS CALENDAR</span>
</nav>

<header>
  <div class="abs brand-name">Events</div>
  <div class="abs brand-slogan">your company slogan here</div>

  <div class="abs account-links">
    <a href="#"><svg width="22" height="22" viewBox="0 0 22 22"><rect x="1" y="9" width="5" height="12"/><path d="M7 9 L11 2 C13 1 14 3 13 5 L12 8 L19 8 C21 8 21 10 20 11 C21 12 21 14 19 14 C20 15 20 17 18 17 C19 18 18 20 16 20 L7 20 Z"/></svg>SIGN UP</a>
    <a href="#"><svg width="20" height="26" viewBox="0 0 20 26"><path d="M4 11 V7 a6 6 0 0 1 12 0 V11 H13 V7 a3 3 0 0 0 -6 0 V11 Z"/><rect x="1" y="11" width="18" height="14" rx="1"/></svg>LOGIN</a>
    <a href="#"><svg width="26" height="26" viewBox="0 0 26 26"><circle cx="13" cy="7" r="6"/><path d="M1 25 C1 16 6 14 13 14 C20 14 25 16 25 25 Z"/></svg>MEMBER</a>
  </div>

  <div class="abs search">
    <div class="search-field">Enter Keyword here</div>
    <div class="search-go">Go</div>
  </div>
</header>

<nav class="abs main-nav">
  <a href="#" style="width:116px;padding-left:41px;">MAIN</a>
  <a href="#" style="width:150px;padding-left:34px;">POPULAR</a>
  <a href="#" style="width:223px;padding-left:30px;">EVENT ORGANIZER</a>
  <a href="#" style="width:130px;padding-left:29px;">FORUM</a>
  <a href="#" style="width:106px;padding-left:28px;">HELP</a>
  <a href="#" style="padding-left:32px;">CONTACT US</a>
</nav>

<div class="abs hero" role="img" aria-label="Photo of an empty conference hall with rows of chairs, projection screens and warm stage lighting"></div>
<div class="abs hero-shade"></div>
<div class="abs hero-arrow prev"><svg width="12" height="18" viewBox="0 0 12 18"><path d="M9 2 L3 9 L9 16" fill="none" stroke="#888" stroke-width="2"/></svg></div>
<div class="abs hero-arrow next"><svg width="12" height="18" viewBox="0 0 12 18"><path d="M3 2 L9 9 L3 16" fill="none" stroke="#888" stroke-width="2"/></svg></div>

<main>
  <div class="abs content-wrap"></div>
  <div class="abs content-panel"></div>

  <h2 class="abs section-title" style="font-weight:400;">Events Organizer</h2>
  <div class="abs section-rule"></div>

  <div class="abs area-select"><span>Area/ Location</span><svg width="14" height="10" viewBox="0 0 14 10"><path d="M0 0 H14 L7 10 Z" fill="#222"/></svg></div>
  <div class="abs area-go">GO</div>

  <article class="abs event-card" style="top:739px;">
    <div class="event-photo" role="img" aria-label="Photo of costumed dancers performing on a stage under green and red lights" style="background:linear-gradient(135deg,#1a8a3a 0%,#2a5a2a 30%,#8a2a4a 55%,#c23a1a 75%,#3a1a2a 100%);"></div>
    <div class="event-details">
      <div class="detail-label" style="top:20px;">Show The Venue :</div>
      <div class="detail-value title" style="top:20px;">Harbour Lantern Hunt on the Tramline</div>
      <div class="detail-value" style="top:46px;">Any Tramline Station<br>Chicago, IL</div>
      <div class="detail-label" style="top:114px;">Date :</div>
      <div class="detail-value" style="top:112px;">20 July 2012</div>
      <div class="detail-label" style="top:161px;">Performance :</div>
      <div class="detail-value" style="top:159px;">E-Commerce is a major progress in technology that has changed the way in which the customers now purchase information, products and the services. I</div>
      <div class="detail-label" style="top:220px;">Speaker :</div>
      <div class="detail-value" style="top:218px;">Marlon Reyes</div>
      <a class="more-link" href="#" style="top:278px;">Clickhere<small>&gt;&gt;</small></a>
      <div class="card-rule" style="top:313px;"></div>
    </div>
  </article>

  <article class="abs event-card" style="top:1092px;">
    <div class="event-photo" role="img" aria-label="Photo of performers in white costumes on a dark stage with blue backlighting" style="background:linear-gradient(135deg,#0a0a1a 0%,#1a1a4a 35%,#3a4a8a 55%,#2a1a3a 75%,#0a0a0a 100%);"></div>
    <div class="event-details">
      <div class="detail-label" style="top:20px;">Show The Venue :</div>
      <div class="detail-value title" style="top:20px;">Harbour Lantern Hunt on the Tramline</div>
      <div class="detail-value" style="top:46px;">Any Tramline Station<br>Chicago, IL</div>
      <div class="detail-label" style="top:114px;">Date :</div>
      <div class="detail-value" style="top:112px;">20 July 2012</div>
      <div class="detail-label" style="top:161px;">Performance :</div>
      <div class="detail-value" style="top:159px;">E-Commerce is a major progress in technology that has changed the way in which the customers now purchase information, products and the services. I</div>
      <div class="detail-label" style="top:220px;">Speaker :</div>
      <div class="detail-value" style="top:218px;">Marlon Reyes</div>
      <a class="more-link" href="#" style="top:278px;">Clickhere<small>&gt;&gt;</small></a>
      <div class="card-rule" style="top:313px;"></div>
    </div>
  </article>

  <article class="abs event-card" style="top:1469px;">
    <div class="event-photo" role="img" aria-label="Photo of an outdoor evening banquet with white-covered tables under green-lit trees" style="background:linear-gradient(180deg,#0a0a0a 0%,#1a3a1a 30%,#3a8a3a 45%,#2a3a8a 70%,#3a4ac2 100%);"></div>
    <div class="event-details">
      <div class="detail-label" style="top:20px;">Show The Venue :</div>
      <div class="detail-value title" style="top:20px;">Harbour Lantern Hunt on the Tramline</div>
      <div class="detail-value" style="top:46px;">Any Tramline Station<br>Chicago, IL</div>
      <div class="detail-label" style="top:114px;">Date :</div>
      <div class="detail-value" style="top:112px;">20 July 2012</div>
      <div class="detail-label" style="top:161px;">Performance :</div>
      <div class="detail-value" style="top:159px;">E-Commerce is a major progress in technology that has changed the way in which the customers now purchase information, products and the services. I</div>
      <div class="detail-label" style="top:220px;">Speaker :</div>
      <div class="detail-value" style="top:218px;">Marlon Reyes</div>
      <a class="more-link" href="#" style="top:278px;">Clickhere<small>&gt;&gt;</small></a>
    </div>
  </article>

  <nav class="abs pagination">
    <span class="current">1</span><span>2</span><span>3</span><span>4</span><span>5</span><span>6</span><span>7</span><span>8</span><span class="next">Next</span>
  </nav>
</main>

<footer>
  <div class="abs site-footer"></div>
  <div class="abs footer-heading" style="left:84px;top:1998px;">Quick Links</div>
  <div class="abs quick-links">
    <div class="quick-row"><span>Hom page</span><span>Login</span><span>Support</span><span>Term &amp; Conditions of Use</span></div>
    <div class="quick-row"><span>Events</span><span>FAQ</span><span>Add Events</span><span>Privacy Policy</span></div>
    <div class="quick-row"><span>Popular</span><span>Login</span><span>Speical Events</span><span>Help</span></div>
    <div class="quick-row"><span>News</span><span>Forgot Password</span><span>Contact info</span><span></span></div>
  </div>
  <div class="abs footer-heading" style="left:798px;top:1998px;">Connect with Us</div>
  <div class="abs social"><span></span><span></span><span></span></div>
  <div class="abs copyright">© 2012 Company Name &nbsp;|&nbsp; All right reserved &nbsp;|&nbsp; Policy Privacy</div>
</footer>

</body>
</html>
```